Web Design Project

We are an IT System Integrator. We provide Korvin 450 ERP System, CRM etc. We also provide hardware, networking servicing. Please look at www.zolvantix.com.sg. They provide the same service as us. We like to redesign our web site. I will attached the color that I prefer for reference.

Our website is www.tadurk.com.sg.  It has been created about 14 years ago.  We are trying to revamp it with a new look and information.   The new website must be informative, fast.    I have attached an attachment which show the color that I prefer(brownish golden).   

Our competitor (www.zolvantix.com) is carrying the same trade as us.  They have all the informations In their website that we will like to have.  Therefore I recommend you to take a look at my competitor website and have a better   
understanding on the kind of information I would like to have for my new website.

This project is guarantee to the person with the best design.  We can have it guarantee.

Target Market(s)

Corporate and companies

Industry/Entity Type

Hardware

```html
<!DOCTYPE html>
<html lang="en">
<head>
<meta charset="utf-8">
<title>Tadurk Information Systems</title>
<link href="https://fonts.googleapis.com/css2?family=PT+Sans:wght@400;700&family=Ubuntu:wght@400;500&display=swap" rel="stylesheet">
<style>
:root{
  --gold:#9a741f;
  --gold-dark:#7a5a16;
  --gold-light:#b0862a;
  --gold-text:#a8801c;
  --caption-gold:#f2c24a;
  --ink:#3a3a3a;
  --muted:#555;
  --line:#d6d6d6;
  --panel:#f2f2f2;
  --footer:#3b3b3b;
  --footer-text:#cfcfcf;
  --badge:#a7a7a7;
}
*{box-sizing:border-box;margin:0;padding:0}
html,body{width:1022px;height:1200px;overflow:hidden}
body{position:relative;background:#f7f7f7;font-family:"PT Sans",sans-serif;color:var(--ink);font-size:12.5px}
.abs{position:absolute}
h2,h3,.nav a,.caption h2{font-family:"Ubuntu",sans-serif;font-weight:500}

.top-bar{left:0;top:0;width:1022px;height:44px;background:linear-gradient(#a07a22,#8e6a1b);border-top:1px solid #c79b3a}
.search{left:803px;top:11px;width:143px;height:24px;background:#fff;border:1px solid #d8c9a4;font-size:10.5px;color:#444;padding:5px 10px}
.search svg{position:absolute;right:8px;top:5px}

.header{left:0;top:44px;width:1022px;height:90px;background:linear-gradient(#fff,#ececec)}
.logo{left:78px;top:70px;display:flex;align-items:center;gap:8px;font-family:"Ubuntu",sans-serif;font-weight:500;font-size:32px;color:var(--gold-light)}
.logo span.dot{width:22px;height:22px;border-radius:50%;background:var(--gold-light)}
.nav{right:76px;top:80px;display:flex}
.nav a{font-size:13.5px;font-weight:400;color:#333;text-decoration:none;padding:0 19px;border-left:1px solid #ccc;line-height:22px}
.nav a:first-child{border-left:0}
.nav a:last-child{padding-right:0}
.nav a.active{color:var(--gold-text)}

.hero-band{left:0;top:134px;width:1022px;height:264px;background:linear-gradient(#9a741f,#6d5013);border-top:3px solid #fff}
.slider{left:77px;top:150px;width:868px;height:310px;background:linear-gradient(100deg,#fff 40%,#ececec 75%,#f8f8f8);border-radius:5px;box-shadow:0 8px 10px -6px rgba(0,0,0,.25)}
.slider-photo{left:5px;top:5px;width:444px;height:303px;background:linear-gradient(90deg,#e7dfd6 0%,#d9d6d3 35%,#8a8b90 60%,#e8e8e8 100%)}
.caption{left:532px;top:65px;width:351px;height:157px;background:rgba(105,105,105,.92);border-radius:3px;padding:20px 18px}
.caption h2{color:var(--caption-gold);font-size:22px;margin-bottom:8px;font-weight:400}
.caption p{color:#fff;font-weight:700;font-size:14.5px;line-height:23px;text-align:justify}
.dots{left:771px;top:275px;display:flex;gap:8px}
.dots i{width:12px;height:12px;border-radius:50%;background:#9c9c9c;border:1px solid #fff;display:block}
.dots i:first-child{background:#555}

.welcome{left:77px;top:495px;width:618px}
.welcome h2{color:var(--gold-text);font-size:19px;margin-bottom:12px}
.welcome p{font-size:12.5px;line-height:21.3px;color:var(--muted);text-align:justify}
.welcome .lead{width:417px}
.welcome .rest{margin-top:10px}
.team-photo{left:509px;top:535px;width:189px;height:115px;border:3px solid #bdbdbd;border-radius:3px;background:linear-gradient(120deg,#c8d3dc,#7e8b96 55%,#e1e4e7)}

.card{top:773px;width:300px;height:253px;background:var(--panel);border:1px solid var(--line);border-radius:3px}
.card-head{height:41px;border-bottom:1px solid var(--line);display:flex;align-items:center;padding:0 16px;gap:12px}
.card-head h3{font-size:19px;color:var(--gold-text);flex:1}
.card-head .more{width:15px;height:15px;border-radius:50%;background:#b5b5b5;position:relative}
.card-head .more::after{content:"";position:absolute;left:5px;top:4px;border-left:5px solid #fff;border-top:3.5px solid transparent;border-bottom:3.5px solid transparent}
.card ul{list-style:none;padding:14px 20px 0 20px}
.card li{margin-bottom:11px;padding-left:16px;position:relative}
.card li::before{content:"";position:absolute;left:2px;top:4px;border-left:5px solid var(--gold-text);border-top:4px solid transparent;border-bottom:4px solid transparent}
.card li b{display:block;color:var(--gold-text);font-weight:400;font-size:12.5px;margin-bottom:7px}
.card li p{font-size:12.5px;line-height:19.5px;color:#333}
.card li time{display:block;font-size:12.5px;color:#555;margin-top:1px}

.partner-badge{left:720px;top:500px;width:227px;height:157px;background:var(--badge);border-radius:3px}
.partner-badge .bar{position:absolute;left:16px;right:16px;bottom:16px;height:38px;background:#f3f3f3;border-radius:6px}
.partner-badge .mark{position:absolute;left:34px;top:20px;width:158px;height:60px;background:#f3f3f3;border-radius:30px}

.focus{left:720px;top:680px;width:227px}
.focus h2{color:var(--gold-text);font-size:19px}
.focus .arrows{position:absolute;right:2px;top:5px}
.quote{margin-top:10px;background:#fff;border:1px solid #ddd;padding:12px 14px;text-align:center;font-size:12.5px;line-height:19.5px;color:#555;height:125px;position:relative}
.quote::after{content:"";position:absolute;right:18px;bottom:-21px;border-left:22px solid transparent;border-top:21px solid #fff}
.author{text-align:right;font-size:12.5px;line-height:18px;color:#333;padding-right:44px;margin-top:10px}

.contact{left:720px;top:901px;width:228px;height:126px;background:linear-gradient(#f0f0f0,#e4e4e4);border:1px solid var(--line);border-radius:3px;padding:10px 15px}
.contact h2{color:var(--gold-text);font-size:19px;margin-bottom:8px}
.contact p{font-size:12px;line-height:25px;color:#444}

.clients{left:0;top:1046px;width:1022px;height:64px;background:linear-gradient(#f4f4f4,#e2e2e2);display:flex;align-items:center;justify-content:center;gap:30px;font-family:"Ubuntu",sans-serif;font-size:18px;color:#8a8a8a}

.footer{left:0;top:1110px;width:1022px;height:90px;background:linear-gradient(#474747,#333);color:var(--footer-text)}
.footer-nav{position:absolute;left:77px;top:22px;display:flex;font-size:12.5px}
.footer-nav a{color:var(--footer-text);text-decoration:none;padding:0 9px;border-left:1px solid #999;line-height:14px}
.footer-nav a:first-child{padding-left:0;border:0}
.copyright{position:absolute;left:77px;top:50px;font-size:12.5px}
.social{position:absolute;right:76px;top:34px;display:flex;gap:6px}
.social i{display:block;width:20px;height:20px;border-radius:3px}
</style>
</head>
<body>
<div class="abs top-bar"></div>
<div class="abs search">Search
  <svg width="14" height="14" viewBox="0 0 14 14"><circle cx="5.5" cy="5.5" r="4" fill="none" stroke="#222" stroke-width="2"/><line x1="8.5" y1="8.5" x2="13" y2="13" stroke="#222" stroke-width="2.5"/></svg>
</div>

<header class="abs header"></header>
<div class="abs logo"><span class="dot"></span>tadurk</div>
<nav class="abs nav">
  <a class="active" href="#">Solutions</a><a href="#">Hardware</a><a href="#">Services</a><a href="#">Clients</a><a href="#">About us</a><a href="#">Contact us</a>
</nav>

<div class="abs hero-band"></div>
<section class="abs slider">
  <div class="abs slider-photo" role="img" aria-label="Smiling businesswoman in front of colleagues working at a laptop"></div>
  <div class="abs caption">
    <h2>Etiam non vehicula sem</h2>
    <p>Phasellus ultricies velit imperdiet accum san posuere. Etiam luctus vel erat sit amet malesuada risus magna, semper.</p>
  </div>
  <div class="abs dots"><i></i><i></i><i></i><i></i></div>
</section>

<section class="abs welcome">
  <h2>Welcome to Tadurk</h2>
  <p class="lead">Nam nisl mauris, accumsan et mauris ut, pharetra sollicitudin magna. Nunc tortor dui, mollis commodo ante in, tincidunt pretium sem. Ut eros urna, commodo ut justo tempor, tempor ullamcorper metus. Duis eros tellus, varius faucibus sodales quis, pellentesque luctus magna. Sed ullamcorper nibh eget turpis adipiscing, non pharetra nulla accumsan. Sed a feugiat tortor. Sed mattis tortor non orci ornare, a commodo justo pretium.</p>
  <p class="rest">Vivamus egestas feugiat orci, ac sodales odio imperdiet nec. Nam tincidunt tempor nunc ac condimentum. Cras vestibu lum nulla ac justo dignissim malesuada. Aenean eu libero tincidunt, eleifend sem egestas, dignissim lorem. Pellentesque adipiscing luctus metus, malesuada ullamcorper metus aliquet eu. Phasellus blandit massa et nulla elementum, quis volutpat massa imperdiet. Donec quis risus justo. Pellentesque at eros a metus eleifend.</p>
</section>
<div class="abs team-photo" role="img" aria-label="Two business colleagues looking at a laptop"></div>

<section class="abs card" style="left:77px">
  <div class="card-head">
    <svg width="23" height="23" viewBox="0 0 23 23"><rect x="1" y="3" width="21" height="19" rx="2" fill="#fff" stroke="#999"/><rect x="1" y="3" width="21" height="5" fill="#c0392b"/><g fill="#999"><rect x="4" y="11" width="3" height="2"/><rect x="10" y="11" width="3" height="2"/><rect x="16" y="11" width="3" height="2"/><rect x="4" y="16" width="3" height="2"/><rect x="10" y="16" width="3" height="2"/><rect x="16" y="16" width="3" height="2"/></g></svg>
    <h3>Latest Events</h3><span class="more"></span>
  </div>
  <ul>
    <li><b>Phasellus blandit massa</b><p>Etiam luctus vel erat sit amet malesuada. Donec risus magna, semper quis augue non.</p><time>July-27-13</time></li>
    <li><b>Phasellus blandit massa</b><p>Etiam luctus vel erat sit amet malesuada. Donec risus magna, semper quis augue non.</p><time>July-27-13</time></li>
  </ul>
</section>

<section class="abs card" style="left:396px">
  <div class="card-head">
    <svg width="26" height="23" viewBox="0 0 26 23"><rect x="1" y="2" width="24" height="20" fill="#eee" stroke="#aaa"/><g fill="#9fb3c8"><rect x="5" y="10" width="3" height="10"/><rect x="10" y="6" width="3" height="14"/><rect x="15" y="12" width="3" height="8"/><rect x="20" y="8" width="3" height="12"/></g></svg>
    <h3>Latest News</h3><span class="more"></span>
  </div>
  <ul>
    <li><b>Phasellus blandit massa</b><p>Etiam luctus vel erat sit amet malesuada. Donec risus magna, semper quis augue non.</p><time>July-27-13</time></li>
    <li><b>Phasellus blandit massa</b><p>Etiam luctus vel erat sit amet malesuada. Donec risus magna, semper quis augue non.</p><time>July-27-13</time></li>
  </ul>
</section>

<aside class="abs partner-badge" role="img" aria-label="Software partner badge"><span class="mark"></span><span class="bar"></span></aside>

<section class="abs focus">
  <h2>Customer Focus</h2>
  <svg class="arrows" width="24" height="12" viewBox="0 0 24 12"><path d="M7 1 2 6l5 5M17 1l5 5-5 5" fill="none" stroke="#888" stroke-width="2"/></svg>
  <blockquote class="quote">"Phasellus ultricies velit imperdiet accumsan posuere. Etiam luctus vel erat sit amet malesuada. Donec risus magna, semper quis augue non, pel lentesque sodales eros. "</blockquote>
  <p class="author">Managiog Director,<br>Halvern Precision Singapore Pte. Ltd.</p>
</section>

<section class="abs contact">
  <h2>Contact us</h2>
  <p>55 Building name, Street name, city</p>
  <p>Call us :&nbsp; 456 321 7790</p>
  <p>Email &nbsp;: &nbsp;info@tadurk.com.sg</p>
</section>

<div class="abs clients">
  <span>Wellmere</span><span>Quorix</span><span>Linvara</span><span>Korvin</span><span>Kaidora</span><span>Betrin</span><span>Halbrecht</span><span>Ardeno</span><span>Cirvel</span>
</div>

<footer class="abs footer">
  <nav class="footer-nav"><a href="#">Home</a><a href="#">Solutions</a><a href="#">Hardware</a><a href="#">Services</a><a href="#">Clients</a><a href="#">About us</a><a href="#">Contact us</a></nav>
  <p class="copyright">Copyright &nbsp;©&nbsp; 2103 &nbsp;&nbsp;Tadurk Information Systems. &nbsp;All rights reserved.</p>
  <div class="social"><i style="background:#4a6aa5" aria-label="Social network link"></i><i style="background:#3fb3e4" aria-label="Social network link"></i></div>
</footer>
</body>
</html>
```